Rapid Pulse Tiny Track Karts

We are looking for a full web site for our race car category that allows us to edit and update some of the content. We would like the site to feel modern and attractive with the following features: 1. Event calender (with the ability for us to update) 2. Social media/ clip wave links 3. photo gallery (with the ability for us to update) 4. Member area with log in access (controlled access) - this area to include access to category regulations for up to 5 types of cars separately 5. Championship ladder for up to 5 different groups 6. sponsor page and sponsors scrolling across bottom of all pages. Please find attached our logo to be used and for reference on color/ style 7. page to show merchandise but no need for a store.

Industry/Entity Type

Motor racing category

Coding

Coded - Design and coding required

Number of Pages Required

5+ page

Colors
0054AA
0677BA
7BADD7
CADEEF
E8F1F8
FFF300
FFF600
FEFA6F
FFFEC7
FFFEE8
EB3D1F
EC4F4E
F09395
F8D3D4
FCEDEE

Requirements
Must have
• Ability to update calender/photo gallery/championship ladder including points/ notice board - Members section

```html
<!DOCTYPE html>
<html lang="en">
<head>
<meta charset="utf-8">
<title>Rapid Pulse Tiny Track Karts</title>
<link href="https://fonts.googleapis.com/css2?family=Bungee&family=Montserrat:ital,wght@0,400;0,500;0,600;0,700;1,600&display=swap" rel="stylesheet">
<style>
:root{
  --blue:#0054AA;--blue-mid:#0677BA;--blue-bright:#1664D9;
  --yellow:#FFF300;--gold:#FCD535;
  --red:#EB3D1F;--red-pure:#F2130F;
  --ink:#111111;--dark:#141414;--grey:#6b6b6b;--line:#e6e6e6;--white:#ffffff;
  --display:'Bungee',sans-serif;--body:'Montserrat',sans-serif;
}
*{box-sizing:border-box;margin:0;padding:0}
html,body{width:1200px;height:4488px;overflow:hidden}
body{position:relative;background:var(--white);font-family:var(--body);color:var(--ink)}
.abs{position:absolute}
.brand{font-family:var(--body);font-weight:700;color:var(--white);display:flex;align-items:center;gap:10px;font-size:19px;line-height:1.1}
.brand-dot{width:16px;height:16px;border-radius:50%;background:var(--red);flex:none}

/* hero */
.hero-photo{left:0;top:0;width:1200px;height:720px;background:radial-gradient(ellipse at 70% 40%,#e24a3a 0%,#2f5fb8 30%,#e8b43a 55%,#3b3b3b 85%)}
.hero-shade{left:0;top:0;width:1200px;height:720px;background:linear-gradient(90deg,rgba(0,0,0,.45),rgba(0,0,0,0) 60%)}
.hero-edge{left:0;top:640px;width:1200px;height:120px}
.hero-base{left:0;top:740px;width:1200px;height:200px;background:var(--white)}
.nav{top:47px;display:flex;gap:0;left:432px;font-size:13px;font-weight:500;color:var(--white)}
.nav a{color:var(--white);text-decoration:none;position:absolute;white-space:nowrap}
.phone-ico{left:910px;top:37px;width:44px;height:44px;border-radius:50%;background:var(--blue-bright);display:flex;align-items:center;justify-content:center}
.phone-txt{left:963px;top:49px;font-size:14px;color:var(--white);font-weight:500}
.kicker-hero{left:383px;top:210px;font-family:var(--body);font-style:italic;font-weight:600;letter-spacing:5px;font-size:22px;color:var(--red-pure)}
.hero-title{left:112px;top:240px;font-family:var(--display);font-size:70px;color:var(--white);line-height:1}
.hero-box{left:108px;top:340px;width:331px;height:66px;background:var(--gold);display:flex;align-items:center;justify-content:center;font-family:var(--body);font-weight:600;font-size:42px;color:var(--blue-bright);letter-spacing:1px}
.btn{display:flex;align-items:center;justify-content:center;color:var(--white);font-weight:600;font-size:17px;border-radius:6px}
.btn-red{left:111px;top:453px;width:192px;height:57px;background:var(--red-pure)}
.btn-blue{left:317px;top:453px;width:125px;height:57px;background:var(--blue-bright)}
.hero-car{left:0;top:636px;width:627px;height:304px;border-radius:48% 52% 40% 45%;background:radial-gradient(ellipse at 40% 45%,#f4a21f,#e2452d 40%,#2a6fbf 70%,rgba(255,255,255,0) 72%)}
.badge{width:100px;height:100px;border-radius:50%}

/* store */
.store-photo{left:111px;top:1008px;width:472px;height:495px;border-radius:6px;background:linear-gradient(160deg,#3f4a53,#6b5a3f 55%,#b6874d)}
.kicker{font-family:var(--body);font-weight:500;font-size:21px;color:var(--red-pure);letter-spacing:.5px}
.title{font-family:var(--display);font-size:40px;color:var(--ink);line-height:1}
.card{width:160px;height:291px;background:var(--white);border-radius:6px;box-shadow:0 4px 22px rgba(0,0,0,.09)}
.card-img{position:absolute;left:26px;top:28px;width:108px;height:120px;border-radius:8px}
.card-name{position:absolute;left:22px;top:208px;font-weight:700;font-size:11px;text-transform:uppercase}
.stars{position:absolute;left:22px;top:225px;display:flex;gap:2px}
.card-price{position:absolute;left:22px;top:247px;font-size:10px;color:var(--red);font-weight:500}
.btn-learn{left:624px;top:1449px;width:158px;height:49px;border-radius:25px;background:var(--red-pure);font-family:var(--display);font-size:14px}

/* events */
.events-bg{left:0;top:1601px;width:1200px;height:956px;background:radial-gradient(ellipse at 50% 55%,#3a3a3a,#161616 70%)}
.ev{width:231px;height:295px}
.ev-photo{width:231px;height:295px}
.ev-text{padding:63px 18px 0 18px}
.ev-num{position:absolute;left:14px;top:-34px;font-family:var(--display);font-size:78px;line-height:1;display:flex;align-items:flex-end;gap:6px}
.ev-num small{font-size:10px;margin-bottom:10px}
.ev h3{font-weight:500;font-size:19px;margin-bottom:12px}
.ev p{font-size:12px;line-height:26px}
.ev .arrow{position:absolute;right:22px;bottom:40px}
.ev-red{background:var(--red-pure);color:var(--white)}
.ev-yellow{background:var(--gold);color:var(--ink)}
.ev-yellow .ev-num{color:var(--blue-bright)}
.ev-blue{background:var(--blue-bright);color:var(--white)}

/* ladder */
.ladder-car{left:985px;top:2600px;width:205px;height:115px;border-radius:40%;background:radial-gradient(ellipse,#e9e9e9,#9aa3b0 45%,rgba(255,255,255,0) 70%)}
.ladder{left:152px;top:2766px;width:897px;border-radius:12px;overflow:hidden;box-shadow:0 6px 24px rgba(0,0,0,.06)}
.row{display:grid;grid-template-columns:281px repeat(10,58.6px) 1fr;align-items:center;height:46px;font-family:var(--display);font-size:16px}
.row span{text-align:center}
.row span:first-child{text-align:left;padding-left:41px;font-family:var(--body);font-size:17px;font-weight:500}
.row.head{height:47px;background:var(--red-pure);color:var(--white);font-family:var(--body);font-weight:600;font-size:13px}
.row.head span{font-family:var(--body);font-size:13px}
.row:nth-child(odd):not(.head){background:#f9f9f9}
.row:not(.head){border-bottom:1px solid #f0f0f0}

/* gallery */
.gal{border-radius:8px}
.dot{width:18px;height:18px;border-radius:50%}

/* footer */
.footer{left:0;top:4046px;width:1200px;height:442px;background:var(--dark)}
.f-logo{left:111px;top:4133px;width:276px;height:100px;border:2px solid var(--white);border-radius:8px;justify-content:center;padding:0 14px}
.f-social{left:168px;top:4272px;width:36px;height:36px;border-radius:50%;background:var(--red-pure)}
.f-head{font-family:var(--display);font-size:19px;color:var(--red-pure)}
.f-link{font-size:14px;color:var(--white)}
.f-field{left:845px;width:243px;border-bottom:1px solid #777;font-size:13px;color:#aaa;padding-bottom:8px}
.btn-sub{left:845px;top:4294px;width:151px;height:40px;border-radius:20px;background:var(--blue-bright);font-family:var(--display);font-size:13px}
.f-rule{left:111px;top:4382px;width:978px;height:1px;background:#333}
.copy{left:0;width:1200px;top:4422px;text-align:center;color:var(--white);font-size:14px}
</style>
</head>
<body>

<!-- hero -->
<div class="abs hero-photo" role="img" aria-label="Blurred photo of miniature race cars on a colourful slot track"></div>
<div class="abs hero-shade"></div>
<svg class="abs hero-edge" viewBox="0 0 1200 120" preserveAspectRatio="none">
  <path d="M0 50 C200 20 400 60 600 40 C800 20 1000 50 1200 10 L1200 120 L0 120 Z" fill="#d9a21a"/>
  <path d="M0 75 C220 50 420 85 620 65 C820 45 1010 75 1200 45 L1200 120 L0 120 Z" fill="#ffffff"/>
</svg>
<div class="abs hero-base"></div>
<div class="abs hero-car" role="img" aria-label="Illustration of a toy monster car with flame paint"></div>
<div class="abs badge" style="left:692px;top:745px;background:#2f7a3e"></div>
<div class="abs badge" style="left:828px;top:745px;background:#f1b81f"></div>
<div class="abs badge" style="left:962px;top:740px;background:#2a6fbf"></div>
<div class="abs badge" style="left:1102px;top:745px;background:#d9dde3"></div>

<div class="abs brand" style="left:113px;top:26px;width:197px;height:70px;border:2px solid #fff;border-radius:8px;padding:0 10px;font-size:15px"><span class="brand-dot"></span>Rapid Pulse Tiny Track Karts</div>
<nav class="abs nav" style="left:0;top:51px">
  <a style="left:432px">Home</a>
  <a style="left:505px">About Us</a>
  <a style="left:601px">Our Services</a>
  <a style="left:716px">Our Blog</a>
  <a style="left:806px">Contact Us</a>
</nav>
<div class="abs phone-ico"><svg width="18" height="18" viewBox="0 0 24 24"><path fill="#fff" d="M6.6 10.8a15.1 15.1 0 0 0 6.6 6.6l2.2-2.2a1 1 0 0 1 1-.25 11.4 11.4 0 0 0 3.6.57 1 1 0 0 1 1 1V20a1 1 0 0 1-1 1A17 17 0 0 1 3 4a1 1 0 0 1 1-1h3.5a1 1 0 0 1 1 1c0 1.25.2 2.45.57 3.57a1 1 0 0 1-.25 1z"/></svg></div>
<div class="abs phone-txt">+1 555 014 2290</div>

<div class="abs kicker-hero">TRACK KARTS</div>
<h1 class="abs hero-title">RAPID PULSE</h1>
<div class="abs hero-box">TINY TRACK</div>
<div class="abs btn btn-red">GET STARTED</div>
<div class="abs btn btn-blue">LOG IN</div>

<!-- store -->
<div class="abs store-photo" role="img" aria-label="Photo of a child playing with rows of miniature cars"></div>
<div class="abs kicker" style="left:634px;top:995px">MERCHANDISE</div>
<h2 class="abs title" style="left:634px;top:1030px">OUR STORE</h2>

<div class="abs card" style="left:622px;top:1113px">
  <div class="card-img" style="background:linear-gradient(#f2f2f2,#dcdcdc)" role="img" aria-label="White t-shirt"></div>
  <div class="card-name">T Shirt</div>
  <div class="stars"><svg width="60" height="10" viewBox="0 0 60 10"><g fill="#f5b400"><circle cx="5" cy="5" r="4"/><circle cx="17" cy="5" r="4"/><circle cx="29" cy="5" r="4"/><circle cx="41" cy="5" r="4"/><circle cx="53" cy="5" r="4"/></g></svg></div>
  <div class="card-price">From $24.70</div>
</div>
<div class="abs card" style="left:803px;top:1113px">
  <div class="card-img" style="background:linear-gradient(#f6f6f6,#e0e0e0)" role="img" aria-label="White mug"></div>
  <div class="card-name">Cup</div>
  <div class="stars"><svg width="60" height="10" viewBox="0 0 60 10"><g fill="#f5b400"><circle cx="5" cy="5" r="4"/><circle cx="17" cy="5" r="4"/><circle cx="29" cy="5" r="4"/><circle cx="41" cy="5" r="4"/><circle cx="53" cy="5" r="4"/></g></svg></div>
  <div class="card-price">From $24.70</div>
</div>
<div class="abs card" style="left:984px;top:1113px">
  <div class="card-img" style="background:linear-gradient(#2f7fd8,#1a4f9e)" role="img" aria-label="Blue backpack"></div>
  <div class="card-name">T Shirt</div>
  <div class="stars"><svg width="60" height="10" viewBox="0 0 60 10"><g fill="#f5b400"><circle cx="5" cy="5" r="4"/><circle cx="17" cy="5" r="4"/><circle cx="29" cy="5" r="4"/><circle cx="41" cy="5" r="4"/><circle cx="53" cy="5" r="4"/></g></svg></div>
  <div class="card-price">From $24.70</div>
</div>
<div class="abs btn btn-learn">LEARN MORE</div>

<!-- events -->
<div class="abs events-bg" role="img" aria-label="Dark photo of a sports car in shadow"></div>
<div class="abs kicker" style="left:0;width:1200px;text-align:center;top:1678px">UPCOMING EVENT</div>
<h2 class="abs title" style="left:0;width:1200px;text-align:center;top:1716px;color:#fff;font-size:42px">EVENT CALENDAR</h2>

<div class="abs ev ev-red" style="left:230px;top:1829px">
  <div class="ev-num">28<small>10 2023</small></div>
  <div class="ev-text"><h3>Lorem Ipsum</h3><p>Lorem ipsum dolor sit amet, consectetur adipiscing elit, sed do eiusmod tempor incididunt ut labore et dolore magna aliqua. Quis ipsum suspendisse ultrices gravida facilisis.</p></div>
  <svg class="arrow" width="14" height="12" viewBox="0 0 14 12"><path d="M0 6h12M7 1l5 5-5 5" stroke="currentColor" stroke-width="1.6" fill="none"/></svg>
</div>
<div class="abs ev-photo" style="left:479px;top:1829px;background:linear-gradient(#3a88c9,#c46b3d 40%,#a85a34)" role="img" aria-label="Photo of a remote control buggy on a dirt track"></div>
<div class="abs ev ev-yellow" style="left:728px;top:1829px">
  <div class="ev-num">30<small style="color:var(--blue-bright)">10 2023</small></div>
  <div class="ev-text"><h3>Lorem Ipsum</h3><p>Lorem ipsum dolor sit amet, consectetur adipiscing elit, sed do eiusmod tempor incididunt ut labore et dolore magna aliqua. Quis ipsum suspendisse ultrices gravida facilisis.</p></div>
  <svg class="arrow" width="14" height="12" viewBox="0 0 14 12"><path d="M0 6h12M7 1l5 5-5 5" stroke="currentColor" stroke-width="1.6" fill="none"/></svg>
</div>
<div class="abs ev-photo" style="left:230px;top:2177px;background:linear-gradient(#6b7a8a,#c23a35 50%,#5e6b78)" role="img" aria-label="Photo of a red toy race car on steps"></div>
<div class="abs ev ev-blue" style="left:479px;top:2177px">
  <div class="ev-num">29<small>10 2023</small></div>
  <div class="ev-text"><h3>Lorem Ipsum</h3><p>Lorem ipsum dolor sit amet, consectetur adipiscing elit, sed do eiusmod tempor incididunt ut labore et dolore magna aliqua. Quis ipsum suspendisse ultrices gravida facilisis.</p></div>
  <svg class="arrow" width="14" height="12" viewBox="0 0 14 12"><path d="M0 6h12M7 1l5 5-5 5" stroke="currentColor" stroke-width="1.6" fill="none"/></svg>
</div>
<div class="abs ev-photo" style="left:728px;top:2177px;background:linear-gradient(150deg,#2f5fb8,#d23c34 50%,#e0b43a)" role="img" aria-label="Photo of a red toy car on a colourful track"></div>

<!-- ladder -->
<div class="abs ladder-car" role="img" aria-label="Illustration of a silver toy formula car"></div>
<div class="abs kicker" style="left:0;width:1200px;text-align:center;top:2648px">CHAMPIONSHIP</div>
<h2 class="abs title" style="left:0;width:1200px;text-align:center;top:2684px;font-size:42px">CHAMPIONSHIP LADDER</h2>
<div class="abs ladder">
  <div class="row head"><span>Team</span><span>GP</span><span>W</span><span>FW</span><span>L</span><span>T</span><span>FL</span><span>GF</span><span>GA</span><span>PTS</span><span>WPCT</span><span></span></div>
  <div class="row"><span>Northern Knights</span><span>8</span><span>5</span><span>0</span><span>1</span><span>2</span><span>0</span><span>38</span><span>19</span><span>12</span><span>0.750</span><span></span></div>
  <div class="row"><span>Northern Knights</span><span>8</span><span>5</span><span>0</span><span>1</span><span>2</span><span>0</span><span>38</span><span>19</span><span>12</span><span>0.750</span><span></span></div>
  <div class="row"><span>Northern Knights</span><span>8</span><span>5</span><span>0</span><span>1</span><span>2</span><span>0</span><span>38</span><span>19</span><span>12</span><span>0.750</span><span></span></div>
  <div class="row"><span>Northern Knights</span><span>8</span><span>5</span><span>0</span><span>1</span><span>2</span><span>0</span><span>38</span><span>19</span><span>12</span><span>0.750</span><span></span></div>
  <div class="row"><span>Northern Knights</span><span>8</span><span>5</span><span>0</span><span>1</span><span>2</span><span>0</span><span>38</span><span>19</span><span>12</span><span>0.750</span><span></span></div>
  <div class="row"><span>Northern Knights</span><span>8</span><span>5</span><span>0</span><span>1</span><span>2</span><span>0</span><span>38</span><span>19</span><span>12</span><span>0.750</span><span></span></div>
  <div class="row"><span>Northern Knights</span><span>8</span><span>5</span><span>0</span><span>1</span><span>2</span><span>0</span><span>38</span><span>19</span><span>12</span><span>0.750</span><span></span></div>
  <div class="row"><span>Northern Knights</span><span>8</span><span>5</span><span>0</span><span>1</span><span>2</span><span>0</span><span>38</span><span>19</span><span>12</span><span>0.750</span><span></span></div>
  <div class="row"><span>Northern Knights</span><span>8</span><span>5</span><span>0</span><span>1</span><span>2</span><span>0</span><span>38</span><span>19</span><span>12</span><span>0.750</span><span></span></div>
</div>

<!-- gallery -->
<div class="abs kicker" style="left:0;width:1200px;text-align:center;top:3324px">OUR GALLERY</div>
<h2 class="abs title" style="left:0;width:1200px;text-align:center;top:3360px;font-size:42px">PHOTO GALLERY</h2>
<div class="abs gal" style="left:111px;top:3454px;width:257px;height:206px;background:linear-gradient(#1c1c1c,#4a4a4a)" role="img" aria-label="Photo of a black formula car in a dark studio"></div>
<div class="abs gal" style="left:380px;top:3454px;width:317px;height:423px;background:linear-gradient(160deg,#1b2733,#1d9ec9 55%,#0e1a24)" role="img" aria-label="Photo of a blue sports car"></div>
<div class="abs gal" style="left:707px;top:3454px;width:382px;height:206px;background:linear-gradient(#d9dde2,#9aa0a6)" role="img" aria-label="Photo of a child with a remote control car on a frozen lake"></div>
<div class="abs gal" style="left:111px;top:3672px;width:257px;height:205px;background:linear-gradient(#7a3a8f,#d42a32 50%,#3b8a3a)" role="img" aria-label="Photo of a red sports car"></div>
<div class="abs gal" style="left:707px;top:3672px;width:159px;height:205px;background:linear-gradient(#5b3a22,#d07a2e)" role="img" aria-label="Photo of a toy buggy in warm light"></div>
<div class="abs gal" style="left:873px;top:3672px;width:216px;height:205px;background:linear-gradient(#d7b79a,#b48560)" role="img" aria-label="Photo of remote control trucks in the desert"></div>
<div class="abs dot" style="left:577px;top:3924px;background:var(--blue-bright)"></div>
<div class="abs dot" style="left:605px;top:3924px;background:#f8d3d4"></div>

<!-- footer -->
<footer class="abs footer"></footer>
<div class="abs brand f-logo"><span class="brand-dot"></span>Rapid Pulse Tiny Track Karts</div>
<div class="abs f-social" aria-label="clip wave"></div>

<div class="abs f-head" style="left:453px;top:4130px">QUICK LINKS</div>
<div class="abs f-link" style="left:453px;top:4190px">›&nbsp; Home</div>
<div class="abs f-link" style="left:453px;top:4220px">›&nbsp; About Us</div>
<div class="abs f-link" style="left:453px;top:4249px">›&nbsp; Our Services</div>
<div class="abs f-link" style="left:453px;top:4279px">›&nbsp; Our Blog</div>
<div class="abs f-link" style="left:453px;top:4310px">›&nbsp; Contact Us</div>

<div class="abs f-head" style="left:651px;top:4130px">HELP LINKS</div>
<div class="abs f-link" style="left:655px;top:4190px">Terms &amp; Conditions</div>
<div class="abs f-link" style="left:655px;top:4220px">Privacy Policy</div>
<div class="abs f-link" style="left:655px;top:4249px">About Us</div>
<div class="abs f-link" style="left:655px;top:4279px">Support</div>

<div class="abs f-head" style="left:843px;top:4130px">NEWSLETTER UPDATES</div>
<div class="abs f-field" style="top:4188px">Name*</div>
<div class="abs f-field" style="top:4239px">Email*</div>
<div class="abs btn btn-sub">SUBMIT NOW</div>

<div class="abs f-rule"></div>
<div class="abs copy">©Copyrights 2023 Rapid Pulse Tiny Track Karts All Rights Reserved</div>

</body>
</html>
```